Tolbek cards

I want a simple business card that pops.
Logo on one side.
On side two i want.
"Are you thinking about a new building on your property, or renovating an existing structure? Contact".....
Owners Name: Dale Whitacre
Owners Phone number: 610-555-0187
Address:4076 Copper Ridge RD, Harlow Mill, PA 17394
Committed to Quality, Service, and Integrity

```html
<!DOCTYPE html>
<html lang="en">
<head>
<meta charset="utf-8">
<title>Tolbek Builders LLC – Business Cards</title>
<link rel="stylesheet" href="https://fonts.googleapis.com/css2?family=Archivo+Black&family=Roboto:wght@400;500;700&display=swap">
<style>
  :root {
    --backdrop: #262626;
    --brown-light: #9a8066;
    --brown-mid: #7a5f47;
    --brown-dark: #5a3f2c;
    --brown-deep: #3f2a1e;
    --tan: #a48a6c;
    --paper: #f1f0ee;
    --paper-shade: #e3e2df;
    --ink: #3a2a20;
    --ink-soft: #4a3a30;
    --rule: #b8b0a8;
    --white: #ffffff;
  }
  * { box-sizing: border-box; margin: 0; padding: 0; }
  html, body { width: 1200px; height: 576px; overflow: hidden; }
  body {
    background: var(--backdrop);
    font-family: "Roboto", Arial, sans-serif;
    position: relative;
  }
  .card {
    position: absolute;
    top: 139px;
    height: 292px;
    border-radius: 12px;
    overflow: hidden;
  }

  /* Front */
  .card-front {
    left: 102px;
    width: 484px;
    background: linear-gradient(180deg, var(--brown-light) 0%, var(--brown-mid) 55%, var(--brown-dark) 100%);
  }
  .brand-name {
    font-family: "Archivo Black", "Arial Black", sans-serif;
    font-weight: 400;
    text-align: center;
    line-height: 1;
  }
  .brand-name .word { display: block; font-size: 48px; letter-spacing: 1px; }
  .brand-name .suffix { display: block; font-size: 16px; letter-spacing: 1.5px; margin-top: 8px; }
  .card-front .brand-name {
    position: absolute;
    left: 0; right: 0;
    top: 148px;
    color: var(--paper);
  }
  .card-front .tagline {
    position: absolute;
    left: 0; right: 0;
    top: 255px;
    display: flex;
    align-items: center;
    justify-content: center;
    gap: 10px;
    color: var(--white);
    font-size: 13px;
    line-height: 16px;
  }
  .tagline-rule {
    width: 70px;
    height: 1px;
    background: linear-gradient(90deg, transparent, var(--paper));
  }
  .tagline-rule.right { background: linear-gradient(90deg, var(--paper), transparent); }

  /* Back */
  .card-back {
    left: 596px;
    width: 480px;
    background: linear-gradient(180deg, var(--paper) 0%, var(--paper-shade) 100%);
  }
  .card-back .wave { position: absolute; inset: 0; }
  .pitch {
    position: absolute;
    left: 22px;
    top: 17px;
    color: var(--white);
    font-size: 13.5px;
    line-height: 18.8px;
    white-space: nowrap;
  }
  .contact {
    position: absolute;
    left: 22px;
    top: 167px;
    width: 174px;
  }
  .contact-label {
    display: flex;
    align-items: center;
    gap: 4px;
    font-size: 9px;
    color: var(--ink-soft);
  }
  .contact-label::after {
    content: "";
    flex: 1;
    height: 1px;
    background: var(--rule);
  }
  .owner-name {
    margin-top: 5px;
    font-size: 21px;
    font-weight: 700;
    color: var(--ink);
    letter-spacing: 0.3px;
    white-space: nowrap;
  }
  .owner-name .surname { color: var(--tan); }
  .contact-line {
    display: flex;
    gap: 6px;
    margin-top: 5px;
    font-size: 13px;
    line-height: 16px;
    color: var(--ink);
    white-space: nowrap;
  }
  .contact-line svg { flex: none; margin-top: 2px; }
  .card-back .brand-name {
    position: absolute;
    left: 230px;
    width: 232px;
    top: 164px;
    color: var(--brown-deep);
  }
  .card-back .brand-name .suffix { margin-top: 6px; }
  .card-back .tagline {
    position: absolute;
    left: 222px;
    width: 248px;
    top: 248px;
    text-align: center;
    font-size: 12px;
    line-height: 16px;
    color: var(--ink);
  }
</style>
</head>
<body>
  <section class="card card-front" aria-label="Card front">
    <h1 class="brand-name"><span class="word">TOLBEK</span><span class="suffix">BUILDERS LLC</span></h1>
    <p class="tagline"><span class="tagline-rule"></span>Committed to Quality, Service &amp; Integrity<span class="tagline-rule right"></span></p>
  </section>

  <section class="card card-back" aria-label="Card back">
    <svg class="wave" width="480" height="292" viewBox="0 0 480 292" aria-hidden="true">
      <path d="M0,0 H480 V18 C400,10 320,18 240,66 C160,114 70,126 0,116 Z" fill="var(--brown-dark)"/>
      <path d="M0,128 C80,136 160,124 240,78 C320,34 400,22 480,30" fill="none" stroke="var(--tan)" stroke-width="6"/>
      <path d="M300,38 C360,16 420,14 460,40" fill="none" stroke="var(--paper)" stroke-width="3"/>
    </svg>
    <p class="pitch">Are you thinking about a new<br>building on your property,<br>or renovating an<br>existing structure?</p>
    <div class="contact">
      <p class="contact-label">Contact:</p>
      <p class="owner-name">DALE <span class="surname">WHITACRE</span></p>
      <p class="contact-line">
        <svg width="11" height="11" viewBox="0 0 12 12" aria-hidden="true"><circle cx="6" cy="6" r="5.3" fill="none" stroke="var(--tan)" stroke-width="1"/><path d="M4,3.2 L5,3 L5.6,4.6 L5,5.2 C5.3,6 6,6.7 6.8,7 L7.4,6.4 L9,7 L8.8,8 C6.2,8.3 3.7,5.8 4,3.2Z" fill="var(--tan)"/></svg>
        <span>610-555-0187</span>
      </p>
      <p class="contact-line">
        <svg width="11" height="12" viewBox="0 0 12 13" aria-hidden="true"><path d="M6,12 C3,8.5 1.5,6.5 1.5,4.8 A4.5,4.5 0 0 1 10.5,4.8 C10.5,6.5 9,8.5 6,12Z" fill="none" stroke="var(--tan)" stroke-width="1.2"/><circle cx="6" cy="4.8" r="1.6" fill="var(--tan)"/></svg>
        <span>4076 Copper Ridge RD,<br>Harlow Mill, PA 17394</span>
      </p>
    </div>
    <h2 class="brand-name"><span class="word">TOLBEK</span><span class="suffix">BUILDERS LLC</span></h2>
    <p class="tagline">Committed to Quality, Service &amp; Integrity</p>
  </section>
</body>
</html>
```